Finding the Root: Reason in Clinical Choice-Crafting

I'd like a cover that looks like it would fit on the shelf next to "The Illness Mirage" by Corwin Talley, "The Close of Forgetting" by Hugh Marchetti, "Meal Mend" by Paul Grieve, "The Energy Restart Plan" by Oscar Pemberley or "The Gland Restart Plan" by the same or "The Cortex Restart Plan" by the same ... either text only (with some interesting fonts that make the title stand out, and the subtitle smaller) or a relevant image, though I'm not entirely sure what that would be since this is a book about big-picture medical decision making.
Author name is Dr Tessa Morrow, NMD
I'll eventually request an e-book, paperback, and audio cover from the winner...

Target Market(s)

practicing physicians

Industry/Entity Type

medicine

Requirements
Must have
• look similar to other books in the genre

```html
<!DOCTYPE html>
<html lang="en">
<head>
<meta charset="utf-8">
<title>Finding the Root — Book Cover</title>
<link rel="stylesheet" href="https://fonts.googleapis.com/css2?family=Cormorant+Garamond:ital,wght@0,500;0,600;0,700;1,500&family=EB+Garamond:wght@400&family=Montserrat:wght@600&display=swap">
<style>
  :root {
    --backdrop: #989898;
    --paper: #fbfaf6;
    --navy: #14203a;
    --sage: #5e7a3a;
    --gold: #c9a85a;
    --mist-green: #d7e2cf;
    --mist-blue: #c9dbe2;
  }
  * { margin: 0; padding: 0; box-sizing: border-box; }
  html, body {
    width: 1200px; height: 1200px; overflow: hidden;
    background: var(--backdrop);
  }
  .cover {
    position: absolute; left: 263px; top: 94px;
    width: 675px; height: 1012px;
    background: var(--paper);
    color: var(--navy);
    font-family: "Cormorant Garamond", Georgia, serif;
  }
  .cover > * { position: absolute; }
  .endorsement {
    top: 28px; left: 0; width: 100%;
    text-align: center;
    font-family: "EB Garamond", Georgia, serif;
    font-size: 15px; line-height: 23px;
  }
  .endorsement-source {
    top: 80px; left: 0; width: 100%;
    text-align: center;
    font-family: "Montserrat", Arial, sans-serif;
    font-size: 12px; letter-spacing: 0.2em;
    color: var(--sage);
  }
  .title-top {
    top: 96px; left: 0; width: 100%;
    text-align: center;
    font-weight: 600; font-size: 150px; line-height: 160px;
    color: var(--navy);
  }
  .title-joiner {
    top: 246px; left: 0; width: 100%;
    text-align: center;
    font-style: italic; font-weight: 500;
    font-size: 46px; line-height: 46px;
  }
  .rule { height: 1px; background: var(--gold); }
  .rule-joiner-left  { top: 268px; left: 163px; width: 131px; }
  .rule-joiner-right { top: 268px; left: 380px; width: 128px; }
  .title-main {
    top: 272px; left: 0; width: 100%;
    text-align: center;
    font-weight: 700; font-size: 240px; line-height: 240px;
    color: var(--sage);
  }
  .rule-subtitle-top    { top: 522px; left: 208px; width: 256px; }
  .rule-subtitle-bottom { top: 654px; left: 208px; width: 256px; }
  .subtitle {
    top: 534px; left: 0; width: 100%;
    text-align: center;
    font-weight: 600; font-size: 28px; line-height: 36px;
    letter-spacing: 0.16em; text-transform: uppercase;
  }
  .subtitle .accent { color: var(--sage); }
  .emblem-band {
    top: 676px; left: 0; width: 100%; height: 200px;
    background:
      radial-gradient(circle at 50% 50%, #ffffff 0 18%, transparent 19%),
      linear-gradient(90deg, var(--mist-green), #eef2ea 45%, #eef2ea 55%, var(--mist-blue));
    opacity: 0.85;
  }
  .rule-author-top    { top: 888px; left: 86px; width: 502px; }
  .rule-author-bottom { top: 943px; left: 86px; width: 502px; }
  .author {
    top: 894px; left: 0; width: 100%;
    text-align: center;
    font-weight: 700; font-size: 38px; line-height: 44px;
    letter-spacing: 0.08em; text-transform: uppercase;
  }
  .tagline {
    top: 958px; left: 0; width: 100%;
    text-align: center;
    font-family: "Montserrat", Arial, sans-serif;
    font-size: 11px; letter-spacing: 0.2em; text-transform: uppercase;
    color: var(--sage);
  }
  .tagline .dot { color: var(--gold); margin: 0 10px; }
</style>
</head>
<body>
  <main class="cover">
    <p class="endorsement">“The right question changes everything.<br>This book will change the way you think about your health.”</p>
    <p class="endorsement-source">— Paul Grieve, MD</p>

    <h1 class="title-top">Finding</h1>
    <div class="rule rule-joiner-left"></div>
    <span class="title-joiner">the</span>
    <div class="rule rule-joiner-right"></div>
    <span class="title-main">Root</span>

    <div class="rule rule-subtitle-top"></div>
    <h2 class="subtitle">Reason in<br><span class="accent">Clinical</span><br>Choice-Crafting</h2>
    <div class="rule rule-subtitle-bottom"></div>

    <div class="emblem-band" role="img" aria-label="Compass rose over flowing green and blue wave lines"></div>

    <div class="rule rule-author-top"></div>
    <p class="author">Dr Tessa Morrow, NMD</p>
    <div class="rule rule-author-bottom"></div>

    <p class="tagline">Better questions<span class="dot">•</span>Better decisions<span class="dot">•</span>Better health</p>
  </main>
</body>
</html>
```